A website for a Maltese Law Firm

Our law firm needs a website to further its business. The site should have a simple yet effective design. We would need the following sections: About us, Practice Areas, About Malta, Contact. These should be further split as follows:

About us: Our firm, Our values, What others say, Offices

Practice Areas: Crimimal, Citizenship & Residence, Sovereign Patron Pathway, Criminal Defence, Civil Litigation, Arbitration and ADR, Commercial and Corporate, Media Law.

About Malta: just one section.

Contact: Just one section

We would also need a news feed at the front of the site to include latest news regarding our cases.

At the bottom we need a section for our Terms and a Privacy Statement.

Our logo is being attached.

Target Market(s)

All clients looking for legal assistance in Malta

Industry/Entity Type

Legal

Coding

Coded - Design and coding required

Number of Pages Required

1 page

Requirements
Must have
• It must be simple yet striking.

```html
<!DOCTYPE html>
<html lang="en">
<head>
<meta charset="utf-8">
<title>Falzon &amp; Grech Advocates</title>
<link rel="stylesheet" href="https://fonts.googleapis.com/css2?family=Cinzel:wght@400;600&family=Open+Sans:wght@400;600;700&display=swap">
<style>
:root{
  --ink:#1b1b1b;
  --ink-deep:#111111;
  --paper:#ffffff;
  --mist:#e9e9e9;
  --card:#e6e6e6;
  --text:#2a2a2a;
  --muted:#bdbdbd;
  --rule:#9a9a9a;
  --hero-a:#3a2412;
  --hero-b:#8a5a2a;
  --hero-c:#c9924a;
}
*{box-sizing:border-box;margin:0;padding:0}
html,body{width:1200px;height:2590px;overflow:hidden}
body{font-family:"Open Sans",Arial,sans-serif;color:var(--text);background:var(--paper);position:relative}
.display{font-family:"Cinzel",Georgia,serif}
section,header,footer{position:absolute;left:0;width:1200px}

/* header */
.site-header{top:0;height:98px;background:var(--ink);color:var(--paper)}
.brand{position:absolute;left:98px;top:24px;font-family:"Cinzel",Georgia,serif;font-size:28px;font-weight:400;letter-spacing:1px;color:var(--paper)}
.brand-rule{position:absolute;left:98px;top:66px;width:282px;height:1px;background:var(--paper);opacity:.6}
.call{position:absolute;right:102px;top:14px;display:flex;align-items:center;gap:12px;font-family:"Cinzel",Georgia,serif;font-size:18px}
.main-nav{position:absolute;right:102px;top:64px;display:flex;font-family:"Cinzel",Georgia,serif;font-size:13.5px;letter-spacing:.5px}
.main-nav a{color:var(--paper);text-decoration:none;padding:0 22px;border-left:1px solid #777;line-height:14px}
.main-nav a:first-child{border-left:0}
.main-nav a:last-child{padding-right:0}

/* hero */
.hero{top:98px;height:515px;background:radial-gradient(ellipse at 80% 55%,#4a2e16 0%,transparent 45%),linear-gradient(100deg,var(--hero-b) 0%,var(--hero-c) 35%,var(--hero-b) 60%,var(--hero-a) 100%)}
.hero-shade{position:absolute;inset:0;background:rgba(0,0,0,.25)}
.hero-title{position:absolute;top:200px;left:0;width:1200px;text-align:center;color:var(--paper);font-family:"Cinzel",Georgia,serif;font-size:31px;line-height:46px;letter-spacing:1px}
.btn-light{position:absolute;top:306px;left:493px;width:214px;height:38px;background:var(--paper);color:var(--ink);font-size:14px;font-weight:600;display:flex;align-items:center;justify-content:center;border-radius:2px}
.slide-arrow{position:absolute;top:237px}

/* about */
.about{top:613px;height:402px;background:var(--mist)}
.portrait-frame{position:absolute;left:98px;top:52px;width:295px;height:302px;background:#d6d6d6;padding:16px}
.portrait{width:100%;height:100%;background:linear-gradient(160deg,#9a9a9a,#5e5e5e 60%,#2d2d2d)}
.about-body{position:absolute;left:440px;top:40px;width:662px}
.section-title{font-family:"Cinzel",Georgia,serif;font-size:33px;font-weight:400;color:var(--ink);letter-spacing:.5px}
.title-rule{position:relative;height:2px;margin-top:8px}
.title-rule::before{content:"";position:absolute;left:0;top:0;width:130px;height:2px;background:var(--ink)}
.title-rule::after{content:"";position:absolute;left:130px;top:1px;width:257px;height:1px;background:var(--rule)}
.about-body p{margin-top:16px;font-size:13.4px;line-height:24.5px}
.bullets{display:flex;gap:32px;margin-top:18px;font-size:14px;font-weight:600;list-style:none}
.bullets li{display:flex;align-items:center;gap:16px}
.bullets li::before{content:"";width:9px;height:9px;border-radius:50%;background:#444}
.btn-dark{display:inline-flex;margin-top:22px;width:111px;height:35px;align-items:center;justify-content:center;background:var(--ink);color:var(--paper);font-size:13px}

/* practice */
.practice{top:1015px;height:504px;background:var(--paper)}
.center-title{text-align:center}
.center-rule{position:relative;width:350px;height:2px;margin:10px auto 0}
.center-rule::before{content:"";position:absolute;left:0;top:1px;width:350px;height:1px;background:#c9c9c9}
.center-rule::after{content:"";position:absolute;left:110px;top:0;width:130px;height:2px;background:var(--ink)}
.practice .center-title{padding-top:40px}
.lede{text-align:center;font-size:13.4px;margin-top:24px}
.cards{position:absolute;left:98px;display:flex;gap:38px}
.practice .cards{top:159px}
.area-card{width:309px;height:300px;background:var(--card);border-bottom:3px solid var(--ink);position:relative;text-align:center}
.area-photo{height:142px}
.area-icon{position:absolute;left:122px;top:114px;width:66px;height:66px;border-radius:50%;background:var(--card);display:flex;align-items:center;justify-content:center}
.area-card h3{font-family:"Cinzel",Georgia,serif;font-weight:400;font-size:19px;color:var(--ink);margin-top:42px}
.area-card p{font-size:13.2px;line-height:19px;margin:12px 26px 0}
.carousel-arrow{position:absolute;top:294px}

/* malta */
.malta{top:1519px;height:311px;background:var(--ink);color:var(--paper)}
.malta-body{position:absolute;left:98px;top:46px;width:604px}
.malta .section-title{color:var(--paper)}
.malta .title-rule::before{background:var(--paper)}
.malta .title-rule::after{display:none}
.malta p{margin-top:16px;font-size:13.4px;line-height:23.5px;color:#e6e6e6}
.btn-outline{display:inline-flex;margin-top:20px;width:111px;height:33px;align-items:center;justify-content:center;border:1px solid var(--paper);font-size:13px;color:var(--paper)}
.malta-photo{position:absolute;left:775px;top:56px;width:327px;height:190px;border:2px solid #cfd9e6;background:linear-gradient(180deg,#2e3f7a 0%,#4f5fa0 40%,#c9773a 62%,#7a3d2a 75%,#1e3e8a 100%)}

/* news */
.news{top:1830px;height:466px;background:var(--mist)}
.news .center-title{padding-top:38px}
.news .cards{top:116px;gap:34px}
.news-card{width:309px}
.news-photo{height:195px;position:relative}
.date-tag{position:absolute;right:16px;top:12px;background:var(--ink);color:var(--paper);font-size:13px;padding:4px 12px}
.news-card h4{font-size:14.4px;font-weight:700;color:var(--ink);margin-top:16px}
.news-card p{font-size:13.2px;line-height:19.5px;margin-top:12px}

/* footer */
.site-footer{top:2296px;height:251px;background:var(--ink);color:#dcdcdc}
.foot-col{position:absolute;top:50px}
.foot-col h5{font-family:"Cinzel",Georgia,serif;font-weight:400;font-size:18px;color:var(--paper);letter-spacing:.5px;padding-bottom:10px;border-bottom:1px solid #3d3d3d}
.quick{left:98px;width:150px}
.quick ul{list-style:none;margin-top:16px;font-size:13px;line-height:27px}
.quick li::before{content:"›";margin-right:12px;color:#aaa}
.contact{left:288px;width:205px}
.contact ul{list-style:none;margin-top:16px;font-size:13px}
.contact li{display:flex;gap:12px;margin-bottom:14px;line-height:19px}
.contact li svg{flex:none;margin-top:3px}
.map{left:568px;width:262px}
.map-box{margin-top:16px;width:262px;height:124px;border:3px solid #f2f2f2;background:linear-gradient(135deg,#e9e4da,#d8dde2 60%,#e6e0cf)}
.divider{position:absolute;top:50px;width:1px;height:160px;background:#3d3d3d}
.foot-brand{position:absolute;left:903px;top:118px;width:200px;text-align:center}
.foot-brand .name{font-family:"Cinzel",Georgia,serif;font-size:19px;color:var(--paper)}
.socials{display:flex;justify-content:center;gap:8px;margin-top:14px}
.socials span{width:25px;height:25px;border-radius:50%;background:#6f7f9a}
.copyright{top:2547px;height:43px;background:var(--ink-deep);color:#cfcfcf;font-size:13px;display:flex;align-items:center;justify-content:center;position:absolute;left:0;width:1200px}
</style>
</head>
<body>

<header class="site-header">
  <div class="brand">Falzon &amp; Grech</div>
  <div class="brand-rule"></div>
  <div class="call">
    <svg width="28" height="28" viewBox="0 0 28 28"><circle cx="14" cy="14" r="12.5" fill="none" stroke="#fff" stroke-width="1.6"/><path d="M10 8.5c.8-.6 1.6-.4 2 .3l1 1.8c.3.6.1 1.2-.4 1.6l-.7.5c.6 1.5 1.8 2.8 3.3 3.5l.6-.7c.4-.5 1-.6 1.6-.3l1.8 1c.7.4.9 1.2.3 2-1 1.3-2.5 1.6-4 .9-3-1.4-5.2-3.8-6.3-6.7-.5-1.4-.2-2.9 .8-3.9z" fill="#fff"/></svg>
    <span>Call: (555)-010-4821</span>
  </div>
  <nav class="main-nav">
    <a>Home</a><a>About Us</a><a>Practice Areas</a><a>About Malta</a><a>Contact Us</a>
  </nav>
</header>

<section class="hero">
  <div role="img" aria-label="Bronze scales of justice in a wood-panelled courtroom" style="position:absolute;inset:0"></div>
  <div class="hero-shade"></div>
  <h1 class="hero-title">The Greatest And Strongest<br>Firm You Can Trust</h1>
  <div class="btn-light">Request A Free Consult</div>
  <svg class="slide-arrow" style="left:41px" width="40" height="40" viewBox="0 0 40 40"><circle cx="20" cy="20" r="18.5" fill="none" stroke="#fff" stroke-width="1.6"/><path d="M23 13l-7 7 7 7" fill="none" stroke="#fff" stroke-width="1.6"/></svg>
  <svg class="slide-arrow" style="left:1120px" width="40" height="40" viewBox="0 0 40 40"><circle cx="20" cy="20" r="18.5" fill="none" stroke="#fff" stroke-width="1.6"/><path d="M17 13l7 7-7 7" fill="none" stroke="#fff" stroke-width="1.6"/></svg>
</section>

<section class="about">
  <div class="portrait-frame"><div class="portrait" role="img" aria-label="Portrait of a senior advocate in a dark suit"></div></div>
  <div class="about-body">
    <h2 class="section-title">About Falzon &amp; Grech</h2>
    <div class="title-rule"></div>
    <p>Lorem ipsum dolor sit amet, consectetuer adipiscing elit, sed diam nonummy nibh euismod tincidunt ut laoreet dolore magna aliquam erat volutpat. Ut wisi enim ad minim veniam, quis nostrud exerci tation ullamcorper suscipit lobortis nisl ut aliquip ex ea commodo consequat. Duis autem vel eum iriure dolor in hendrerit in vulputate velit esse molestie consequat, vel illum dolore eu feugiat nulla facilisis at vero eros et accumsan et iusto odio dignissim qui blandit praesent luptatum zzril delenit augue duis dolore te feugait nulla facilisi.</p>
    <ul class="bullets"><li>Our Firms</li><li>Our Values</li></ul>
    <div class="btn-dark">Read More</div>
  </div>
</section>

<section class="practice">
  <h2 class="section-title center-title">Our Practice Areas</h2>
  <div class="center-rule"></div>
  <p class="lede">Lorem ipsum dolor sit amet, consectetur adipisicing elit. Obcaecati laborum ipsa, a voluptates libero possimus sapiente.</p>
  <svg class="carousel-arrow" style="left:54px" width="20" height="40" viewBox="0 0 20 40"><path d="M16 4L4 20l12 16" fill="none" stroke="#555" stroke-width="1.6"/></svg>
  <svg class="carousel-arrow" style="left:1126px" width="20" height="40" viewBox="0 0 20 40"><path d="M4 4l12 16L4 36" fill="none" stroke="#555" stroke-width="1.6"/></svg>
  <div class="cards">
    <article class="area-card">
      <div class="area-photo" role="img" aria-label="Law books with a gavel and scales" style="background:linear-gradient(135deg,#5a3a1e,#a8783e 55%,#3b2614)"></div>
      <div class="area-icon"><svg width="30" height="30" viewBox="0 0 30 30"><circle cx="9" cy="17" r="6" fill="none" stroke="#111" stroke-width="2.4"/><circle cx="21" cy="17" r="6" fill="none" stroke="#111" stroke-width="2.4"/><path d="M12 9h6" stroke="#111" stroke-width="2.4"/></svg></div>
      <h3>Criminal Law</h3>
      <p>Sed ut perspiciatis unde omnis iste natus error sit voluptatem accusantium omnis unde doloremque laudantium</p>
    </article>
    <article class="area-card">
      <div class="area-photo" role="img" aria-label="Passports resting on a world map" style="background:linear-gradient(135deg,#c9c2b2,#8a2a22 50%,#2a1a22)"></div>
      <div class="area-icon"><svg width="30" height="30" viewBox="0 0 30 30"><path d="M15 4L3 15h4v11h6v-7h4v7h6V15h4z" fill="#111"/></svg></div>
      <h3>Citizenship And Residence</h3>
      <p>Sed ut perspiciatis unde omnis iste natus error sit voluptatem accusantium omnis unde doloremque laudantium</p>
    </article>
    <article class="area-card">
      <div class="area-photo" role="img" aria-label="Columned courthouse facade under blue sky" style="background:linear-gradient(180deg,#2f5fa8,#8ea8cc 45%,#d9d2c2)"></div>
      <div class="area-icon"><svg width="30" height="30" viewBox="0 0 30 30"><path d="M15 3L3 9v2h24V9z" fill="#111"/><path d="M6 13h3v10H6zm5 0h3v10h-3zm5 0h3v10h-3zm5 0h3v10h-3zM3 24h24v3H3z" fill="#111"/></svg></div>
      <h3>Civil Litigation</h3>
      <p>Sed ut perspiciatis unde omnis iste natus error sit voluptatem accusantium omnis unde doloremque laudantium</p>
    </article>
  </div>
</section>

<section class="malta">
  <div class="malta-body">
    <h2 class="section-title">About Malta</h2>
    <div class="title-rule"></div>
    <p>Lorem ipsum dolor sit amet, consectetur adipiscing elit, sed do eiusmod tempor incididunt ut labore et dolore magna aliqua. Ut enim ad minim veniam, quis nostrud exercitation ullamco laboris nisi ut aliquip ex ea commodo consequat. Duis aute irure dolor in reprehenderit in voluptate velit esse cillum dolore eu fugiat nulla pariatur. Excepteur sint occaecat cupidatat non proident, sunt in culpa qui officia deserunt mollit anim id est laborum.</p>
    <div class="btn-outline">Read More</div>
  </div>
  <div class="malta-photo" role="img" aria-label="Valletta harbour skyline lit at dusk"></div>
</section>

<section class="news">
  <h2 class="section-title center-title">Latest News</h2>
  <div class="center-rule"></div>
  <div class="cards">
    <article class="news-card">
      <div class="news-photo" role="img" aria-label="Lawyer signing documents beside a gavel" style="background:linear-gradient(135deg,#2a2a2a,#6a5a48 55%,#2b2018)"><span class="date-tag">08, June</span></div>
      <h4>We denounce with righteous indignation and.</h4>
      <p>At vero eos et accusamus et iusto odio dignissimos ducimus qui blanditiis praesentium voluptatum deleniti atque corrupti quos dolores et.</p>
    </article>
    <article class="news-card">
      <div class="news-photo" role="img" aria-label="Scales of justice on a courtroom desk" style="background:linear-gradient(135deg,#c9924a,#6a3a1a 55%,#3a2212)"><span class="date-tag">08, June</span></div>
      <h4>We denounce with righteous indignation and.</h4>
      <p>At vero eos et accusamus et iusto odio dignissimos ducimus qui blanditiis praesentium voluptatum deleniti atque corrupti quos dolores et.</p>
    </article>
    <article class="news-card">
      <div class="news-photo" role="img" aria-label="Close view of marble columns" style="background:linear-gradient(90deg,#8a8a86,#e4e2dc 30%,#9a9894 55%,#ecebe6 80%,#7a7874)"><span class="date-tag">08, June</span></div>
      <h4>We denounce with righteous indignation and.</h4>
      <p>At vero eos et accusamus et iusto odio dignissimos ducimus qui blanditiis praesentium voluptatum deleniti atque corrupti quos dolores et.</p>
    </article>
  </div>
</section>

<footer class="site-footer">
  <div class="foot-col quick">
    <h5>Quick Links</h5>
    <ul><li>Home</li><li>About Us</li><li>Practice Areas</li><li>About Malta</li><li>Contact Us</li></ul>
  </div>
  <div class="divider" style="left:260px"></div>
  <div class="foot-col contact">
    <h5>Contact Detail</h5>
    <ul>
      <li><svg width="12" height="16" viewBox="0 0 12 16"><path d="M6 0a6 6 0 0 0-6 6c0 4.5 6 10 6 10s6-5.5 6-10a6 6 0 0 0-6-6zm0 8.5A2.5 2.5 0 1 1 6 3.5a2.5 2.5 0 0 1 0 5z" fill="#fff"/></svg><span>12/4, Harbour Lane, Valletta<br>88, Orchard Street, Birkirkara</span></li>
      <li><svg width="13" height="13" viewBox="0 0 13 13"><path d="M2.5 0.5l2 3-1.2 1.3c.8 1.8 2.2 3.2 4 4l1.2-1.2 3 2-1 2.2C5 11.5 1.5 8 .5 1.7z" fill="#fff"/></svg><span>(555) -010 - 4821</span></li>
      <li><svg width="14" height="13" viewBox="0 0 14 13"><rect x="3" y="0" width="8" height="4" fill="#fff"/><rect x="0" y="4" width="14" height="6" rx="1" fill="#fff"/><rect x="3" y="8" width="8" height="5" fill="#fff" stroke="#1b1b1b"/></svg><span>(555) -010 - 4830</span></li>
      <li><svg width="14" height="10" viewBox="0 0 14 10"><rect width="14" height="10" fill="#fff"/><path d="M0 0l7 6 7-6" fill="none" stroke="#1b1b1b"/></svg><span>info@fgadvocates.example</span></li>
    </ul>
  </div>
  <div class="divider" style="left:528px"></div>
  <div class="foot-col map">
    <h5>Location Map</h5>
    <div class="map-box" role="img" aria-label="Street map showing the office location"></div>
  </div>
  <div class="divider" style="left:868px"></div>
  <div class="foot-brand">
    <div class="name">Falzon &amp; Grech</div>
    <div class="socials"><span></span><span></span><span></span><span></span></div>
  </div>
</footer>
<div class="copyright">Copyright © 2016 - Falzon &amp; Grech Advocates, All Rights Reserved.</div>

</body>
</html>
```